Help us stand out from the crowd - Court of Maywell

We are a luxury watch business and are looking to develop our own paperwork that we can issue with our watches etc. I am looking for the following documents to be designed: Invoice, Warranty card, Insurance valuation, instruction booklet and a small folder to keep it all in. Need it to be small though. I have attached some images of my friends ones that look fantastic.

Target Market(s)

High net worth watch enthusiasts

Requirements
Must have
• Must be clean, precise and very easy on the eye. Think Vornel but underpinned with a classic british feel.
Should not have
• Shouldn't be dark.

```html
<!DOCTYPE html>
<html lang="en">
<head>
<meta charset="utf-8">
<title>Invoice – Court of Maywell</title>
<link rel="stylesheet" href="https://fonts.googleapis.com/css2?family=Urbanist:wght@300;400;500&display=swap">
<style>
  :root {
    --backdrop: #5e5e5e;
    --paper: #ffffff;
    --ink: #1e1e1e;
    --ink-soft: #3a3a3a;
    --rule: #4a4a4a;
    --ring: #f2f2f2;
    --caption: #ffffff;
  }
  * { margin: 0; padding: 0; box-sizing: border-box; }
  html, body {
    width: 1200px; height: 1200px; overflow: hidden;
    background: var(--backdrop);
    font-family: "Urbanist", sans-serif;
  }
  .canvas { position: relative; width: 1200px; height: 1200px; }
  .invoice {
    position: absolute; left: 204px; top: 39px;
    width: 790px; height: 996px;
    background: var(--paper); overflow: hidden;
    color: var(--ink);
  }
  .invoice__rings { position: absolute; inset: 0; }
  .invoice > *:not(.invoice__rings) { position: absolute; }

  .invoice__title { left: 53px; top: 60px; font-size: 47px; font-weight: 300; letter-spacing: 0.5px; line-height: 1; }

  .brand { left: 56px; top: 136px; }
  .brand__name {
    font-size: 32px; font-weight: 400; line-height: 1;
    color: var(--ink); white-space: nowrap;
  }
  .brand__tagline {
    margin-top: 14px;
    font-size: 15px; font-weight: 300; line-height: 1;
    color: var(--ink-soft); white-space: nowrap;
  }
  .contact { left: 56px; top: 230px; font-size: 19.5px; font-weight: 300; line-height: 23px; color: var(--ink-soft); }

  .meta { left: 56px; top: 335px; font-size: 20px; font-weight: 300; line-height: 22.5px; color: var(--ink-soft); }
  .meta__row { display: flex; }
  .meta__label { width: 124px; }

  .client { left: 554px; top: 303px; width: 184px; }
  .client__label { text-align: right; font-size: 19px; font-weight: 400; padding-right: 5px; color: var(--ink-soft); }
  .client__line { height: 26.5px; border-bottom: 1px solid var(--rule); }
  .client__line:first-of-type { height: 15px; }

  .items { left: 55px; top: 509px; width: 683px; border-collapse: collapse; }
  .items th { font-size: 22.5px; font-weight: 500; text-align: left; height: 40px; vertical-align: top; border-bottom: 1px solid var(--rule); color: var(--ink-soft); }
  .items td { font-size: 19.5px; font-weight: 300; height: 32px; border-bottom: 1px solid var(--rule); color: var(--ink-soft); }
  .items .col-product { width: 190px; padding-left: 1px; }
  .items .col-qty { width: 202px; text-align: center; }
  .items .col-price { width: 110px; text-align: center; }
  .items .col-total { text-align: right; }

  .totals { left: 472px; top: 770px; width: 266px; font-size: 21px; font-weight: 500; color: var(--ink-soft); }
  .totals__row { display: flex; justify-content: space-between; height: 29px; align-items: center; }
  .totals__label { width: 92px; text-align: center; }
  .totals__row--grand { border-top: 1px solid var(--rule); margin-top: 1px; height: 41px; padding-top: 6px; }

  .thanks { left: 55px; top: 935px; font-size: 19.7px; font-weight: 300; line-height: 22.5px; color: var(--ink-soft); }

  .caption {
    position: absolute; left: 0; right: 0; top: 1081px;
    text-align: center; font-size: 54.5px; font-weight: 500;
    color: var(--caption); letter-spacing: 0.5px; line-height: 1;
  }
</style>
</head>
<body>
<div class="canvas">
  <section class="invoice">
    <svg class="invoice__rings" width="790" height="996" viewBox="0 0 790 996" aria-hidden="true">
      <circle cx="790" cy="42" r="327" fill="none" stroke="var(--ring)" stroke-width="50"/>
      <circle cx="-48" cy="1147" r="419" fill="none" stroke="var(--ring)" stroke-width="50"/>
    </svg>

    <h1 class="invoice__title">INVOICE</h1>

    <div class="brand">
      <div class="brand__name">Court of Maywell</div>
      <div class="brand__tagline">Fine timepieces, kept with care</div>
    </div>

    <div class="contact">
      <div>www.courtofmaywell.com &nbsp;| &nbsp;(+31) 620418395</div>
      <div>Havenkade 27, 3011 KL Rotterdam, Netherlands</div>
    </div>

    <div class="meta">
      <div class="meta__row"><span class="meta__label">Invoice date</span><span>-</span></div>
      <div class="meta__row"><span class="meta__label">Invoice net</span><span>-</span></div>
      <div class="meta__row"><span class="meta__label">Currency</span><span>-</span></div>
    </div>

    <div class="client">
      <div class="client__label">Client</div>
      <div class="client__line"></div>
      <div class="client__line"></div>
      <div class="client__line"></div>
      <div class="client__line"></div>
    </div>

    <table class="items">
      <thead>
        <tr><th class="col-product">Product</th><th class="col-qty">Quantity</th><th class="col-price">Price</th><th class="col-total">TOTAL</th></tr>
      </thead>
      <tbody>
        <tr><td class="col-product">Name</td><td class="col-qty">2</td><td class="col-price">1000</td><td class="col-total">$2000</td></tr>
        <tr><td></td><td></td><td></td><td></td></tr>
        <tr><td></td><td></td><td></td><td></td></tr>
        <tr><td></td><td></td><td></td><td></td></tr>
        <tr><td></td><td></td><td></td><td></td></tr>
      </tbody>
    </table>

    <div class="totals">
      <div class="totals__row"><span class="totals__label">SUBTOTAL</span><span>$2000</span></div>
      <div class="totals__row"><span class="totals__label">TAX</span><span>10%</span></div>
      <div class="totals__row totals__row--grand"><span class="totals__label">TOTAL</span><span>$1800</span></div>
    </div>

    <p class="thanks">(Client name), thank you very much.<br>We really appreciate your business.</p>
  </section>

  <p class="caption">PLEASE CHECK YOU MESSAGES.</p>
</div>
</body>
</html>
```